Harborline Auto LLC

Car Dealer Customer Service
Address: 2874 Cresthaven Road, Shelbyville, TN 37162
web: www.harborlineautoxq.net
email: harborlineautoxq@mailnest.example
Phone: (931) 555-0148
Phone: (629) 555-0173

```html
<!DOCTYPE html>
<html lang="en">
<head>
<meta charset="utf-8">
<title>Harborline Auto – Business Card</title>
<link rel="stylesheet" href="https://fonts.googleapis.com/css2?family=Montserrat:wght@700;800&family=Roboto:wght@400&family=Rubik:wght@800&display=swap">
<style>
  :root {
    --page-bg: #1b1b1b;
    --white: #ffffff;
    --brand-blue: #1e77ab;
    --band-top: #2890ca;
    --band-bottom: #1c74a8;
    --accent: #e9b044;
  }
  * { margin: 0; padding: 0; box-sizing: border-box; }
  html, body { width: 1075px; height: 1200px; overflow: hidden; background: var(--page-bg); }
  .card {
    position: absolute;
    left: 206px;
    width: 663px;
    height: 395px;
    overflow: hidden;
    box-shadow: 3px 3px 0 rgba(0,0,0,0.85);
  }
  .card--front { top: 187px; background: var(--white); }
  .card--back { top: 637px; background: linear-gradient(180deg, var(--band-top), var(--band-bottom)); }

  .brand-mark { position: absolute; border-radius: 50%; }
  .card--front .brand-mark { left: 420px; top: 40px; width: 110px; height: 110px; background: var(--brand-blue); }
  .card--back .brand-mark { left: 262px; top: 72px; width: 140px; height: 140px; background: var(--white); }

  .brand-name { position: absolute; font-family: "Montserrat", sans-serif; font-weight: 800; white-space: nowrap; }
  .card--front .brand-name { right: 41px; top: 178px; font-size: 29px; color: var(--brand-blue); }
  .card--back .brand-name { left: 0; right: 0; top: 250px; text-align: center; font-size: 40px; color: var(--white); }

  .person { position: absolute; left: 35px; top: 204px; }
  .person__name { font-family: "Montserrat", sans-serif; font-weight: 800; font-size: 23px; color: var(--brand-blue); line-height: 1.1; }
  .person__title { font-family: "Roboto", sans-serif; font-size: 18px; color: var(--accent); line-height: 1.1; }
  .person__rule { position: absolute; left: 35px; top: 261px; width: 219px; height: 5px; background: var(--accent); }

  .contact-band { position: absolute; left: 0; right: 0; top: 264px; bottom: 0; background: linear-gradient(180deg, var(--band-top), var(--band-bottom)); }
  .contact-list { position: absolute; left: 35px; top: 32px; list-style: none; font-family: "Roboto", sans-serif; font-size: 18px; color: var(--white); line-height: 23px; }
  .contact-list li { display: flex; align-items: center; gap: 6px; }
  .contact-list svg { width: 18px; height: 18px; flex: none; }
  .location { position: absolute; right: 40px; top: 26px; text-align: right; font-family: "Roboto", sans-serif; font-size: 18px; color: var(--white); line-height: 23px; }
  .location__web { margin-bottom: 6px; }

  .tagline-band { position: absolute; left: 0; right: 0; bottom: 0; height: 57px; background: var(--accent); display: flex; align-items: center; justify-content: center; }
  .tagline { font-family: "Rubik", sans-serif; font-weight: 800; font-size: 27px; letter-spacing: 2px; color: var(--white); text-transform: uppercase; }
</style>
</head>
<body>
  <section class="card card--front">
    <div class="brand-mark"></div>
    <div class="brand-name">HARBORLINE AUTO</div>

    <div class="person">
      <div class="person__name">MARCUS DELANEY</div>
      <div class="person__title">Managing Director</div>
    </div>
    <div class="person__rule"></div>

    <div class="contact-band">
      <ul class="contact-list">
        <li>
          <svg viewBox="0 0 24 24" aria-hidden="true"><path fill="#fff" d="M6.6 10.8a15 15 0 0 0 6.6 6.6l2.2-2.2c.3-.3.7-.4 1-.2 1.1.4 2.3.6 3.6.6.6 0 1 .4 1 1V20c0 .6-.4 1-1 1A17 17 0 0 1 3 4c0-.6.4-1 1-1h3.5c.6 0 1 .4 1 1 0 1.3.2 2.5.6 3.6.1.3 0 .7-.2 1z"/></svg>
          (931) 555-0148
        </li>
        <li>
          <svg viewBox="0 0 24 24" aria-hidden="true"><path fill="#fff" d="M6.6 10.8a15 15 0 0 0 6.6 6.6l2.2-2.2c.3-.3.7-.4 1-.2 1.1.4 2.3.6 3.6.6.6 0 1 .4 1 1V20c0 .6-.4 1-1 1A17 17 0 0 1 3 4c0-.6.4-1 1-1h3.5c.6 0 1 .4 1 1 0 1.3.2 2.5.6 3.6.1.3 0 .7-.2 1z"/></svg>
          (629) 555-0173
        </li>
        <li>
          <svg viewBox="0 0 24 24" aria-hidden="true"><rect x="2" y="5" width="20" height="14" fill="#fff"/><path d="M2 5l10 8 10-8" fill="none" stroke="#1c74a8" stroke-width="1.6"/></svg>
          harborlineautoxq@mailnest.example
        </li>
      </ul>
      <div class="location">
        <div class="location__web">www.harborlineautoxq.net</div>
        <div>2874 Cresthaven Road</div>
        <div>Shelbyville, TN 37162</div>
      </div>
    </div>
  </section>

  <section class="card card--back">
    <div class="brand-mark"></div>
    <div class="brand-name">HARBORLINE AUTO</div>
    <div class="tagline-band"><span class="tagline">Car Dealer Customer Service</span></div>
  </section>
</body>
</html>
```